Rice importer and exporter. We need a new design for a 18 kg plastic bag.

We want to create a new brand of rice. This type of rice is produced in southeast Asia, imported to Portugal and sold to the local market. The target are people 30+ years old of all ethnicity. The name of the brand should be 'Marevo', this is the name we want people to see and get used to it. <br/>Regarding the package itself. We want a simple bag, not with many different colours (3, 4 or 5) with preference to golden yellow. The Front page, should have our brand 'Marevo' and the exact description of the type of rice 'Arroz 100% Jasmin Perfumado' and 'Premium Quality'. In the bag should also be included the nutrition facts, cooking instructions, a trasnparent part where customer can see the quality of the product and the our company info. Finally we would like to see in the front page the five stars and on the back the triple AAA (see examples of attached files). All the remaining should be of your imagination. <br/>Finally, the image 3 is an example of a bag structure that we want to make.

Target Market(s)

People 30+ years old

Font styles to use
Serif
Sans Serif

Colors
ffc214
fec214
fee18a
fbee3f
faef58
fbf289

Requirements
Must have
• 5 Stars on the front page, triple A's on the back and a transparent area for the customers to see the quality of the rice.

```html
<!DOCTYPE html>
<html lang="en">
<head>
<meta charset="utf-8">
<title>Marevo – 18 kg Rice Bag Artwork</title>
<link rel="stylesheet" href="https://fonts.googleapis.com/css2?family=Alegreya+Sans:wght@700;800&family=Barlow:wght@400;500&display=swap">
<style>
  :root {
    --gold: #fec214;
    --orange: #e07b0c;
    --ribbon: #f49322;
    --brown: #8a5a12;
    --label: #d9820f;
    --white: #ffffff;
    --page: #ffffff;
    --icon-grey: #c9cfd1;
    --serif-sans: "Alegreya Sans", sans-serif;
    --din: "Barlow", sans-serif;
  }
  * { margin: 0; padding: 0; box-sizing: border-box; }
  html, body { width: 1104px; height: 1200px; overflow: hidden; background: var(--page); }
  .artboard { position: relative; width: 1104px; height: 1200px; }
  .panel-slot { position: absolute; top: 286px; width: 517px; height: 627px; }
  .panel-slot.front-slot { left: 17px; }
  .panel-slot.back-slot { left: 570px; }
  .panel {
    position: absolute; left: 0; top: 0; width: 834px; height: 1011px;
    background: var(--gold); transform: scale(0.62); transform-origin: 0 0;
    font-family: var(--din); overflow: hidden;
  }
  .abs { position: absolute; }

  /* front */
  .front-frame { left: 31px; top: 37px; width: 773px; height: 937px; border: 12px solid var(--orange); border-radius: 60px; }
  .ribbon { left: 40px; top: 100px; }
  .ribbon-title { left: 0; width: 834px; top: 112px; text-align: center; font-family: var(--serif-sans); font-weight: 800; font-size: 40px; color: var(--white); letter-spacing: 1px; }
  .product-window { left: 214px; top: 200px; width: 460px; height: 340px; border-radius: 46% 46% 50% 50% / 40% 40% 60% 60%;
    background: radial-gradient(ellipse at 45% 35%, #fbfaf5 0%, #ece6d6 38%, #c9a25a 62%, #b98a3e 80%, rgba(254,194,20,0) 100%); }
  .heart { left: 86px; top: 288px; }
  .loved { left: 112px; top: 458px; transform: translate(-50%, -50%) rotate(-90deg); white-space: nowrap; font-size: 24px; color: var(--orange); letter-spacing: 0.5px; }
  .brand-name { left: 0; width: 834px; top: 540px; text-align: center; font-family: var(--serif-sans); font-weight: 800; font-size: 136px; color: var(--white); line-height: 1; }
  .stars { left: 230px; top: 700px; }
  .rice-type { left: 200px; width: 434px; top: 828px; text-align: center; font-family: var(--serif-sans); font-weight: 800; font-size: 33px; color: var(--white); line-height: 42px; letter-spacing: 0.5px; }
  .net-label { left: 624px; top: 820px; font-size: 30px; color: var(--orange); }
  .net-value { left: 622px; top: 850px; font-size: 62px; font-weight: 500; color: var(--orange); }

  /* back */
  .section-title { font-size: 27px; color: var(--brown); letter-spacing: 0.5px; }
  .cook-title { left: 89px; top: 92px; }
  .cook-rule { left: 60px; top: 128px; width: 338px; height: 3px; background: var(--label); }
  .step-num { left: 60px; width: 26px; height: 26px; border-radius: 50%; background: var(--white); color: var(--orange); font-size: 15px; font-weight: 500; text-align: center; line-height: 26px; }
  .step-icon { left: 100px; width: 92px; height: 72px; border-radius: 12px; }
  .step-icon.basin { background: linear-gradient(180deg, #98a6a6 0%, #c9cfd1 55%, #ffffff 100%); }
  .step-icon.rinse { background: linear-gradient(180deg, #98a6a6 0%, #e6e9ea 70%, #7fb9e0 100%); }
  .step-icon.water { background: linear-gradient(180deg, #98a6a6 0%, #4aa3dc 55%, #ffffff 100%); }
  .step-icon.cooker { background: linear-gradient(180deg, #e57b1a 0%, #e6e9ea 45%, #c9cfd1 100%); }
  .step-icon.bowl { background: linear-gradient(180deg, #f6f3ea 0%, #c98b5c 50%, #9b3d18 100%); }
  .step-text { left: 212px; font-size: 17.5px; line-height: 20px; color: var(--brown); }

  .nutrition-box { left: 439px; top: 80px; width: 336px; height: 608px; background: var(--white); border-radius: 16px; }
  .nutri-title { left: 0; width: 336px; top: 12px; text-align: center; color: var(--label); font-size: 27px; }
  .nutri-rule { left: 13px; top: 48px; width: 311px; height: 3px; background: var(--label); }
  .nutri-divider { left: 260px; top: 62px; width: 2px; height: 532px; background: var(--label); }
  .nutri-row { left: 18px; width: 236px; font-size: 12px; line-height: 14px; color: var(--label); }
  .nutri-val { left: 274px; font-size: 12px; line-height: 14px; color: var(--label); }

  .seal-arc { left: 50px; top: 720px; }
  .served-bowl { left: 88px; top: 772px; width: 154px; height: 125px; border-radius: 50% 50% 46% 46% / 40% 40% 60% 60%;
    background: linear-gradient(180deg, #f8f4ea 0%, #efe6d2 38%, #b86a26 45%, #8c4513 100%); }
  .grade { left: 0; width: 330px; top: 906px; text-align: center; font-size: 58px; color: var(--orange); font-weight: 500; }
  .storage { left: 277px; top: 830px; font-size: 17px; line-height: 20px; color: var(--label); }
  .origin-map { left: 442px; top: 738px; width: 114px; height: 114px; border-radius: 50%; background: radial-gradient(circle at 45% 50%, #ffffff 0%, #eef3f6 55%, #c9dde8 100%); }
  .company-info { left: 584px; top: 744px; font-size: 17px; line-height: 20.3px; color: var(--label); }
</style>
</head>
<body>
<main class="artboard">

  <section class="panel-slot front-slot">
    <div class="panel front">
      <div class="abs front-frame"></div>

      <svg class="abs ribbon" width="760" height="110" viewBox="0 0 760 110" aria-hidden="true">
        <polygon points="0,45 130,40 130,108 100,100 128,110 60,88" fill="#e9851a"/>
        <polygon points="760,45 630,40 630,108 660,100 632,110 700,88" fill="#e9851a"/>
        <path d="M70,38 Q380,20 690,38 L690,78 Q380,62 70,78 Z" fill="var(--ribbon)"/>
        <rect x="0" y="45" width="132" height="46" fill="var(--ribbon)"/>
        <rect x="628" y="45" width="132" height="46" fill="var(--ribbon)"/>
      </svg>
      <div class="abs ribbon-title">PREMIUM QUALITY</div>

      <div class="abs product-window" role="img" aria-label="Clear window showing a bowl of white jasmine rice with a cream flower"></div>

      <svg class="abs heart" width="54" height="48" viewBox="0 0 54 48" aria-hidden="true">
        <path d="M27,47 C10,34 0,24 0,13 C0,5 6,0 13,0 C19,0 24,4 27,9 C30,4 35,0 41,0 C48,0 54,5 54,13 C54,24 44,34 27,47 Z" fill="var(--orange)"/>
      </svg>
      <div class="abs loved">LOVED WORLDWIDE</div>

      <div class="abs brand-name">Marevo</div>

      <svg class="abs stars" width="420" height="100" viewBox="0 0 420 100" aria-hidden="true" fill="var(--orange)">
        <defs>
          <polygon id="star" points="0,-1 0.2245,-0.309 0.951,-0.309 0.363,0.118 0.588,0.809 0,0.382 -0.588,0.809 -0.363,0.118 -0.951,-0.309 -0.2245,-0.309"/>
        </defs>
        <use href="#star" transform="translate(29,45) scale(30)"/>
        <use href="#star" transform="translate(104,48) scale(34)"/>
        <use href="#star" transform="translate(189,55) scale(38)"/>
        <use href="#star" transform="translate(272,48) scale(34)"/>
        <use href="#star" transform="translate(349,45) scale(30)"/>
      </svg>

      <div class="abs rice-type">ARROZ 100%<br>JASMIN PERFUMADO</div>
      <div class="abs net-label">NET WT.</div>
      <div class="abs net-value">18 kg</div>
    </div>
  </section>

  <section class="panel-slot back-slot">
    <div class="panel back">
      <div class="abs section-title cook-title">COOKING INSTRUCTION</div>
      <div class="abs cook-rule"></div>

      <div class="abs step-num" style="top:167px">1</div>
      <div class="abs step-icon basin" style="top:166px" role="img" aria-label="Illustration of rice being scooped into the rice basin"></div>
      <div class="abs step-text" style="top:183px">Scoop 3 cups of rice<br>(for family of 4) into<br>the rice basin</div>

      <div class="abs step-num" style="top:278px">2</div>
      <div class="abs step-icon rinse" style="top:282px" role="img" aria-label="Illustration of rinsing rice in the basin"></div>
      <div class="abs step-text" style="top:287px">Rinse rice just ONCE</div>

      <div class="abs step-num" style="top:389px">3</div>
      <div class="abs step-icon water" style="top:392px" role="img" aria-label="Illustration of water added to the rice basin"></div>
      <div class="abs step-text" style="top:394px">Add water 3.9 cups<br>(ratio water 1.3 : rice 1)<br>into the rice basin.</div>

      <div class="abs step-num" style="top:500px">4</div>
      <div class="abs step-icon cooker" style="top:494px" role="img" aria-label="Illustration of a rice cooker switched on"></div>
      <div class="abs step-text" style="top:490px">Placing the rice basin in<br>the rice cooker &amp; switch<br>cooker on. Do'nt lift lid<br>or stir rice while cooking.</div>

      <div class="abs step-num" style="top:611px">5</div>
      <div class="abs step-icon bowl" style="top:606px" role="img" aria-label="Illustration of a bowl of cooked rice"></div>
      <div class="abs step-text" style="top:607px">When rice is cooked,<br>leave for 15 minute<br>the fluff with a fork.<br>Serve hot &amp; fragrant.</div>

      <div class="abs nutrition-box">
        <div class="abs section-title nutri-title">NUTRITION FACTS</div>
        <div class="abs nutri-rule"></div>
        <div class="abs nutri-divider"></div>

        <div class="abs nutri-row" style="top:66px">Average nutritional per /<br>Durchschnittliche Nährwertangaben je /<br>gemiddelde voedingswaarden per /<br>Valeurs nutritionelles moyennes par /<br>Gennemsitlig naeringsvarndi pr. /<br>Valor nutricional medio por</div>
        <div class="abs nutri-val" style="top:66px">100 gr</div>

        <div class="abs nutri-row" style="top:165px">Energy / Energie / energie / énergie<br>energi / wartość energetyczna / energiaa</div>
        <div class="abs nutri-val" style="top:165px">1482 kJ/<br>349 kcal</div>

        <div class="abs nutri-row" style="top:208px">Fat / Fett / Vetten / matières grasses /<br>fedt / thuszczu / rasvaa / grassi / grasas /<br>Lipidos</div>
        <div class="abs nutri-val" style="top:208px">0.6 g</div>

        <div class="abs nutri-row" style="top:264px">Of which saturates / davon gesättigte<br>Fettsäuren / Warrvan verzadigd vetzuren /<br>Di cui acidi grassi saturi / delas cuales<br>saturados / dos qui acidos gordos<br>saturados</div>
        <div class="abs nutri-val" style="top:264px">0.2 g</div>

        <div class="abs nutri-row" style="top:348px">Carbohydrate / Kohlenhydrat /<br>koolhydraten / glucides / kullhydrat /<br>węglowodany / hiilihydraatti / Carboidrati<br>/ hidratos de carbono / hidratos de<br>carbono</div>
        <div class="abs nutri-val" style="top:348px">79 g</div>

        <div class="abs nutri-row" style="top:431px">Of which sugars / davon Zucker / waarvan<br>suikers / heraf sukkerarter / w tym cukry<br>/ josta sokererita / di cui zuccheri / de los<br>cuales azucares / dos quais / açúcares</div>
        <div class="abs nutri-val" style="top:431px">0 g</div>

        <div class="abs nutri-row" style="top:503px">Fibre / Faser / Vezel / Fiber / Kuitu / Fibra</div>
        <div class="abs nutri-val" style="top:503px">0.7 g</div>

        <div class="abs nutri-row" style="top:530px">Protein / Eiewiß / eiwitten / biatko /<br>proteiinia</div>
        <div class="abs nutri-val" style="top:530px">7.0 g</div>

        <div class="abs nutri-row" style="top:571px">Salt / Salz / zout / sel / sól / suolaa / sale</div>
        <div class="abs nutri-val" style="top:571px">0 g</div>
      </div>

      <svg class="abs seal-arc" width="230" height="140" viewBox="0 0 230 140" aria-hidden="true">
        <defs><path id="seal-path" d="M20,125 A100,100 0 0 1 212,110"/></defs>
        <text font-family="Alegreya Sans, sans-serif" font-weight="700" font-size="27" fill="var(--label)" letter-spacing="2">
          <textPath href="#seal-path">PREMIUM QUALITY</textPath>
        </text>
      </svg>
      <div class="abs served-bowl" role="img" aria-label="Wooden bowl filled with cooked white rice"></div>
      <div class="abs grade">AAA</div>
      <div class="abs storage">STORE IN A COOL<br>AND DRY PLACE</div>

      <div class="abs origin-map" role="img" aria-label="Map of Cambodia with the national flag marking the country of origin"></div>
      <div class="abs company-info">PRODUCT OF CAMBODIA<br>IMPORTADO POR :<br>Tavira &amp; Sol Lda<br>Rua das Oliveiras<br>pavilhão B4 2700-101<br>Amadora Portugal<br><br>T. 912-000-345<br>E. info@tavirasol.pt</div>
    </div>
  </section>

</main>
</body>
</html>
```